GJ & DW Fencing Pty Ltd

We already have an existing logo created by Pixel Harbour however we have restructured to a company. We would like someone to add Pty Ltd to our business name please.

Colors

Designer to choose only greyscale colors for use in the design.

```html
<!DOCTYPE html>
<html lang="en">
<head>
<meta charset="utf-8">
<title>GJ &amp; DW Fencing Pty Ltd — Business Card</title>
<link href="https://fonts.googleapis.com/css2?family=Merriweather:wght@400;700&display=swap" rel="stylesheet">
<style>
  :root {
    --backdrop: #1b1c1e;
    --card: #26292b;
    --card-deep: #131415;
    --ink-light: #f2f2f2;
    --ink-muted: #cfcfcf;
    --rule: #e6e6e6;
  }
  * { margin: 0; padding: 0; box-sizing: border-box; }
  html, body {
    width: 1200px; height: 800px; overflow: hidden;
    background: var(--backdrop);
    font-family: "Merriweather", Georgia, serif;
  }
  .canvas {
    position: relative; width: 1200px; height: 800px;
    display: flex; align-items: center; justify-content: center; gap: 40px;
  }
  .card {
    position: relative; width: 520px; height: 300px;
    background: var(--card);
    box-shadow: 0 14px 30px rgba(0,0,0,.45);
    overflow: hidden;
  }
  /* brand name set as plain text */
  .brand-name {
    position: absolute;
    font-weight: 700; font-size: 30px; line-height: 1; letter-spacing: .3px;
    white-space: nowrap;
  }
  .card--front .brand-name {
    left: 50%; top: 50%; transform: translate(-50%, -50%);
    color: var(--card-deep);
  }
  .card--back .brand-name {
    right: 36px; top: 62px; font-size: 28px;
    color: var(--ink-light);
  }
  .card--back .divider {
    position: absolute; left: 160px; right: 32px; top: 178px;
    height: 1.5px; background: var(--rule);
  }
  .holder {
    position: absolute; left: 30px; top: 160px; color: var(--ink-light);
  }
  .holder__name { font-weight: 700; font-size: 14px; letter-spacing: 1px; text-transform: uppercase; }
  .holder__role { font-size: 12px; color: var(--ink-muted); margin-top: 4px; }
  .company {
    position: absolute; right: 32px; top: 192px; text-align: right; color: var(--ink-light);
  }
  .company__name { font-weight: 700; font-size: 12px; }
  .company__address { font-size: 11px; color: var(--ink-muted); margin-top: 5px; }
  .contacts {
    position: absolute; left: 30px; top: 222px; list-style: none;
    color: var(--ink-muted); font-size: 11.5px;
  }
  .contacts li { display: flex; align-items: center; gap: 8px; margin-bottom: 7px; }
  .contacts svg { width: 16px; height: 16px; flex: none; }
</style>
</head>
<body>
<main class="canvas">
  <section class="card card--front" aria-label="Business card front">
    <span class="brand-name">GJ &amp; DW Fencing Pty Ltd</span>
  </section>

  <section class="card card--back" aria-label="Business card back">
    <span class="brand-name">GJ &amp; DW Fencing Pty Ltd</span>
    <div class="holder">
      <p class="holder__name">Liam Porter</p>
      <p class="holder__role">President</p>
    </div>
    <div class="divider"></div>
    <div class="company">
      <p class="company__name">GJ &amp; DW Fencing Pty Ltd</p>
      <p class="company__address">PO Box 418 Merredin WA 6415</p>
    </div>
    <ul class="contacts">
      <li>
        <svg viewBox="0 0 16 16" aria-hidden="true"><circle cx="8" cy="8" r="8" fill="#f2f2f2"/><rect x="5.5" y="3.5" width="5" height="9" rx="1" fill="none" stroke="#26292b" stroke-width="1.2"/><line x1="7" y1="10.8" x2="9" y2="10.8" stroke="#26292b" stroke-width="1"/></svg>
        <span>Mob 0412 558 903</span>
      </li>
      <li>
        <svg viewBox="0 0 16 16" aria-hidden="true"><circle cx="8" cy="8" r="8" fill="#f2f2f2"/><rect x="4" y="5" width="8" height="6" fill="none" stroke="#26292b" stroke-width="1.2"/><polyline points="4,5 8,8.5 12,5" fill="none" stroke="#26292b" stroke-width="1.2"/></svg>
        <span>gjdwfencing@mailbox.com</span>
      </li>
    </ul>
  </section>
</main>
</body>
</html>
```